How likely are people to engage in social distancing? We need a good illustration to show the data!

We surveyed U.S. adults March 20th - 24th, 2020 and asked how likely they were to engage in social distancing (and other COVID-19 related health behaviors). What did the survey find? Basically, most people intend to engage in social distancing behaviors (e.g., avoiding large crowds) and other behaviors that reduce the spread of COVID-19 (e.g., washing hands at least 20 seconds). When most people intend to engage in a behavior, then public health professionals try to leverage that to move more people to act.
Now we need innovative and professional images that attempt to communicate one or all of these findings. The specific findings are nicely summarized in the attached document. For example, 82% of participants intend to engage in social distancing.
What sort of visual are we looking for? Our preference is for an original illustration (or set of illustrations). Our preference is for (creative and powerful illustrations, but we are also open to the creative and well-executed infographics.
We need these images fast . We will award monetary prizes to the 3 best designs. If we like more than that, then we might purchase more (e.g., in past contests, we have purchased as many as 30 designs).
What we will need:
(1) The illustrations must be original and we will need the photoshop and/or illustrator files for all artwork.
(2) You can illustrate all of the findings or just one of them. We need creative approaches that do a lucid job of bringing the data to life. Most people intend to engage in these behaviors. How to communicate that? Republicans and Democrats do not differ in their intentions; how to communicate that?
(3) The illustration should say, somewhere: "Based on a survey of 400 U.S. adults conducted March 20 - 24th, 2020."

U.S. Adults

• Original illustrations based on the findings of the survey (see attached document).

```html
<!DOCTYPE html>
<html lang="en">
<head>
<meta charset="utf-8">
<title>Social Distancing Intentions</title>
<link href="https://fonts.googleapis.com/css2?family=Anton&family=Arimo:wght@400;700&family=Gochi+Hand&family=Open+Sans:ital,wght@0,700;1,700&display=swap" rel="stylesheet">
<style>
:root{
  --teal:#2fc2a9;
  --navy:#0a5282;
  --red:#d2404a;
  --track:#d1d2d4;
  --yellow:#fcdb2c;
  --title-yellow:#fde74c;
  --pale-yellow:#fff5a8;
  --pale-blue:#cdf3fb;
  --ink:#1d1d1b;
  --white:#ffffff;
  --figure:#9aa3ad;
  --figure-warm:#d8a86a;
}
*{margin:0;padding:0;box-sizing:border-box}
html,body{width:1200px;height:2288px;overflow:hidden;background:var(--white)}
.canvas{position:relative;width:1200px;height:2288px;font-family:"Arimo",sans-serif;color:var(--ink)}

.banner{position:absolute;border-radius:36px;text-align:center}
.banner--teal{left:31px;top:16px;width:1136px;height:222px;background:var(--teal)}
.banner--yellow{left:28px;top:867px;width:1143px;height:184px;background:var(--yellow)}
.banner__title{font-family:"Anton",sans-serif;font-weight:400;font-size:40px;color:var(--title-yellow);-webkit-text-stroke:1.6px var(--ink);paint-order:stroke fill;letter-spacing:.3px;line-height:1}
.banner--teal .banner__title{margin-top:30px}
.banner--yellow .banner__title{margin-top:18px}
.banner__quote{font-family:"Gochi Hand",sans-serif;font-size:38px;line-height:52px;margin-top:14px}
.banner--teal .banner__quote{color:var(--white)}
.banner--yellow .banner__quote{color:var(--ink);margin-top:8px}

/* overall bars */
.stat{position:absolute;height:92px;width:333px;background:var(--track)}
.stat__fill{position:absolute;left:0;top:0;height:92px;display:flex;align-items:center;gap:12px;color:var(--white);padding-left:16px;overflow:hidden}
.stat--navy .stat__fill{background:var(--navy)}
.stat--red .stat__fill{background:var(--red)}
.stat__pct{font-family:"Anton",sans-serif;font-size:38px;line-height:1;flex:none}
.stat__label{font-size:16px;line-height:20px;white-space:nowrap}
.icon{position:absolute;border-radius:14px;opacity:.85}

.question{position:absolute;left:0;width:1200px;text-align:center}
.question__title{font-family:"Anton",sans-serif;font-weight:400;font-size:54px;line-height:1;-webkit-text-stroke:1.8px var(--ink);paint-order:stroke fill}
.question__title--teal{color:var(--teal)}
.question__title--yellow{color:var(--title-yellow)}
.question__answer{font-family:"Open Sans",sans-serif;font-style:italic;font-weight:700;font-size:31px;margin-top:14px}

/* comparison */
.side{position:absolute;top:1111px;height:960px}
.side--rep{left:28px;width:590px;background:var(--pale-yellow)}
.side--dem{left:618px;width:555px;background:var(--pale-blue)}
.tab{position:absolute;top:1073px;width:298px;height:60px;text-align:center;font-family:"Anton",sans-serif;font-size:42px;line-height:68px}
.tab--rep{left:178px;background:var(--pale-yellow);color:var(--red)}
.tab--dem{left:718px;background:var(--pale-blue);color:var(--navy)}

.cmp{position:absolute;height:71px;background:var(--white)}
.cmp--rep{left:139px;width:346px}
.cmp--dem{left:711px;width:347px}
.cmp__fill{position:absolute;top:0;height:71px;color:var(--white);font-size:18px;line-height:22px;display:flex;flex-direction:column;justify-content:center;white-space:nowrap}
.cmp--rep .cmp__fill{right:0;background:var(--red);padding-left:11px}
.cmp--dem .cmp__fill{left:0;background:var(--navy);padding-right:11px;text-align:right}
.cmp__pct{position:absolute;font-family:"Anton",sans-serif;font-size:50px;line-height:71px;height:71px}
.cmp__pct--rep{left:38px;color:var(--red)}
.cmp__pct--dem{left:1068px;color:var(--navy)}
.mascot{position:absolute;width:90px;height:110px;border-radius:40px 40px 12px 12px}
.mascot--rep{left:468px;background:var(--figure)}
.mascot--dem{left:675px;width:56px;background:var(--figure-warm)}
.midicon{position:absolute;left:575px;width:80px;height:80px}

.footer{position:absolute;left:31px;top:2221px;width:1141px;height:50px;background:var(--red);color:var(--white);font-family:"Open Sans",sans-serif;font-weight:700;font-size:17px;text-align:center;line-height:50px}
</style>
</head>
<body>
<div class="canvas">

  <header class="banner banner--teal">
    <h1 class="banner__title">Percent of Americans intending to engage in social distancing</h1>
    <p class="banner__quote">“We would like to know how likely it is that you will perform<br>these behaviors to slow the spread of coronavirus?”</p>
  </header>

  <div class="icon" role="img" aria-label="Two figures separated by a double arrow" style="left:88px;top:262px;width:140px;height:76px;background:linear-gradient(90deg,#3fb89a,#f0c63c,#f4a340)"></div>
  <div class="icon" role="img" aria-label="Figure working on a laptop beside a window" style="left:115px;top:374px;width:90px;height:90px;background:linear-gradient(135deg,#5aa9e0,#c9c9c9)"></div>
  <div class="icon" role="img" aria-label="Figure avoiding a large crowd" style="left:88px;top:492px;width:145px;height:92px;background:linear-gradient(90deg,#e98a92,#8d9aa6)"></div>
  <div class="icon" role="img" aria-label="Crossed out party drinks sign" style="left:106px;top:617px;width:112px;height:98px;border-radius:50%;background:#e7c3c5"></div>

  <div class="icon" role="img" aria-label="Two small figures separated by a ruler" style="left:606px;top:283px;width:132px;height:32px;background:linear-gradient(90deg,#f0a040,#f2dc48,#3fb89a)"></div>
  <div class="icon" role="img" aria-label="Figure washing hands next to a timer" style="left:622px;top:370px;width:118px;height:100px;background:linear-gradient(135deg,#f0d040,#d9eef8)"></div>
  <div class="icon" role="img" aria-label="Hand sanitizer bottle with a tick" style="left:650px;top:498px;width:80px;height:90px;background:linear-gradient(180deg,#e3eef5,#5aaee0)"></div>
  <div class="icon" role="img" aria-label="Figure touching face next to a cross" style="left:628px;top:617px;width:118px;height:96px;background:linear-gradient(90deg,#3fb89a,#e0686e)"></div>

  <div class="stat stat--navy" style="left:251px;top:254px"><div class="stat__fill" style="width:268px"><span class="stat__pct">81%</span><span class="stat__label">intend to<br>Engage in social<br>distancing</span></div></div>
  <div class="stat stat--red" style="left:251px;top:373px"><div class="stat__fill" style="width:273px"><span class="stat__pct">82%</span><span class="stat__label">intend to<br>Work from Home</span></div></div>
  <div class="stat stat--navy" style="left:251px;top:493px"><div class="stat__fill" style="width:209px"><span class="stat__pct">63%</span><span class="stat__label">intend to<br>Avoid large<br>gatherings</span></div></div>
  <div class="stat stat--red" style="left:251px;top:613px"><div class="stat__fill" style="width:282px"><span class="stat__pct">85%</span><span class="stat__label">intend to<br>Cancel social activities</span></div></div>

  <div class="stat stat--navy" style="left:763px;top:254px"><div class="stat__fill" style="width:270px"><span class="stat__pct">81%</span><span class="stat__label">intend to<br>Put distance between<br>yourself and other<br>people</span></div></div>
  <div class="stat stat--red" style="left:763px;top:373px"><div class="stat__fill" style="width:284px"><span class="stat__pct">85%</span><span class="stat__label">intend to<br>Wash hands at least<br>20 seconds</span></div></div>
  <div class="stat stat--navy" style="left:763px;top:493px"><div class="stat__fill" style="width:290px"><span class="stat__pct">87%</span><span class="stat__label">intend to<br>Use hand sanitizer</span></div></div>
  <div class="stat stat--red" style="left:763px;top:613px"><div class="stat__fill" style="width:284px"><span class="stat__pct">85%</span><span class="stat__label">intend to<br>Avoid touching your<br>eyes, nose, and mouth</span></div></div>

  <section class="question" style="top:738px">
    <h2 class="question__title question__title--teal">What does this data say?</h2>
    <p class="question__answer">It says that most people intend to engage in these behaviors.</p>
  </section>

  <header class="banner banner--yellow">
    <h2 class="banner__title">Comparing Republicans and Democrats</h2>
    <p class="banner__quote">“We would like to know how likely it is that you will perform<br>these behaviors to slow the spread of coronavirus?”</p>
  </header>

  <div class="side side--rep"></div>
  <div class="side side--dem"></div>
  <div class="tab tab--rep">REPUBLICANS</div>
  <div class="tab tab--dem">DEMOCRATS</div>

  <div class="cmp__pct cmp__pct--rep" style="top:1154px">82%</div>
  <div class="cmp cmp--rep" style="top:1154px"><div class="cmp__fill" style="width:282px">intend to<br>Engage in social distancing</div></div>
  <div class="cmp cmp--dem" style="top:1154px"><div class="cmp__fill" style="width:280px">intend to<br>Engage in social distancing</div></div>
  <div class="cmp__pct cmp__pct--dem" style="top:1154px">81%</div>
  <svg class="midicon" style="top:1150px" viewBox="0 0 80 80" aria-hidden="true"><path d="M4 40 L18 30 L18 36 L62 36 L62 30 L76 40 L62 50 L62 44 L18 44 L18 50 Z" fill="#f2dc48" stroke="#1d1d1b" stroke-width="2"/></svg>

  <div class="cmp__pct cmp__pct--rep" style="top:1272px">60%</div>
  <div class="cmp cmp--rep" style="top:1272px"><div class="cmp__fill" style="width:205px">intend to<br>Work from Home</div></div>
  <div class="cmp cmp--dem" style="top:1272px"><div class="cmp__fill" style="width:223px">intend to<br>Work from Home</div></div>
  <div class="cmp__pct cmp__pct--dem" style="top:1272px">65%</div>
  <svg class="midicon" style="top:1264px" viewBox="0 0 80 80" aria-hidden="true"><rect x="6" y="8" width="68" height="64" fill="#d2404a" stroke="#1d1d1b" stroke-width="3"/><rect x="14" y="16" width="24" height="20" fill="#fff"/><rect x="44" y="16" width="22" height="20" fill="#fff"/><rect x="14" y="44" width="24" height="20" fill="#fff"/><rect x="44" y="44" width="22" height="20" fill="#fff"/></svg>

  <div class="cmp__pct cmp__pct--rep" style="top:1390px">85%</div>
  <div class="cmp cmp--rep" style="top:1390px"><div class="cmp__fill" style="width:293px">intend to<br>Avoid large gatherings</div></div>
  <div class="cmp cmp--dem" style="top:1390px"><div class="cmp__fill" style="width:291px">intend to<br>Avoid large gatherings</div></div>
  <div class="cmp__pct cmp__pct--dem" style="top:1390px">84%</div>
  <div class="midicon" role="img" aria-label="Crowd at a concert" style="top:1384px;border-radius:14px;background:linear-gradient(180deg,#8d9aa6,#4b5a66)"></div>

  <div class="cmp__pct cmp__pct--rep" style="top:1509px">82%</div>
  <div class="cmp cmp--rep" style="top:1509px"><div class="cmp__fill" style="width:282px">intend to<br>Cancel social activities</div></div>
  <div class="cmp cmp--dem" style="top:1509px"><div class="cmp__fill" style="width:277px">intend to<br>Cancel social activities</div></div>
  <div class="cmp__pct cmp__pct--dem" style="top:1509px">80%</div>
  <div class="midicon" role="img" aria-label="Crossed out party drinks sign" style="top:1506px;border-radius:50%;background:#e7c3c5"></div>

  <div class="cmp__pct cmp__pct--rep" style="top:1627px">84%</div>
  <div class="cmp cmp--rep" style="top:1627px"><div class="cmp__fill" style="width:289px">intend to<br>Put distance between yourself<br>and other people</div></div>
  <div class="cmp cmp--dem" style="top:1627px"><div class="cmp__fill" style="width:302px">intend to<br>Put distance between yourself<br>and other people</div></div>
  <div class="cmp__pct cmp__pct--dem" style="top:1627px">87%</div>
  <div class="midicon" role="img" aria-label="Ruler held between the two characters" style="top:1672px;height:22px;left:578px;width:95px;background:#f2dc48;border:2px solid #1d1d1b"></div>

  <div class="cmp__pct cmp__pct--rep" style="top:1745px">87%</div>
  <div class="cmp cmp--rep" style="top:1745px"><div class="cmp__fill" style="width:300px">intend to<br>Wash hands at least 20 seconds</div></div>
  <div class="cmp cmp--dem" style="top:1745px"><div class="cmp__fill" style="width:305px">intend to<br>Wash hands at least 20 seconds</div></div>
  <div class="cmp__pct cmp__pct--dem" style="top:1745px">88%</div>
  <svg class="midicon" style="top:1742px" viewBox="0 0 80 80" aria-hidden="true"><circle cx="40" cy="40" r="34" fill="#fff" stroke="#1d1d1b" stroke-width="3"/><path d="M40 40 L40 6 A34 34 0 0 1 70 24 Z" fill="#d2404a" stroke="#1d1d1b" stroke-width="2"/></svg>

  <div class="cmp__pct cmp__pct--rep" style="top:1863px">87%</div>
  <div class="cmp cmp--rep" style="top:1863px"><div class="cmp__fill" style="width:300px">intend to<br>Use hand sanitizer</div></div>
  <div class="cmp cmp--dem" style="top:1863px"><div class="cmp__fill" style="width:291px">intend to<br>Use hand sanitizer</div></div>
  <div class="cmp__pct cmp__pct--dem" style="top:1863px">84%</div>
  <svg class="midicon" style="top:1862px" viewBox="0 0 80 80" aria-hidden="true"><path d="M8 42 L30 64 L74 16 L64 10 L30 48 L18 34 Z" fill="#7cc242" stroke="#1d1d1b" stroke-width="3" stroke-linejoin="round"/></svg>

  <div class="cmp__pct cmp__pct--rep" style="top:1982px">80%</div>
  <div class="cmp cmp--rep" style="top:1982px"><div class="cmp__fill" style="width:276px">intend to<br>Avoid touching your<br>eyes, nose, and mouth</div></div>
  <div class="cmp cmp--dem" style="top:1982px"><div class="cmp__fill" style="width:284px">intend to<br>Avoid touching your<br>eyes, nose, and mouth</div></div>
  <div class="cmp__pct cmp__pct--dem" style="top:1982px">82%</div>
  <svg class="midicon" style="top:1982px" viewBox="0 0 80 80" aria-hidden="true"><path d="M18 10 L40 30 L62 10 L72 20 L50 40 L72 60 L62 70 L40 50 L18 70 L8 60 L30 40 L8 20 Z" fill="#d2404a"/></svg>

  <div class="mascot mascot--rep" style="top:1120px" role="img" aria-label="Cartoon elephant in a suit"></div>
  <div class="mascot mascot--dem" style="top:1110px;height:122px" role="img" aria-label="Cartoon donkey in a suit"></div>
  <div class="mascot mascot--rep" style="top:1244px" role="img" aria-label="Cartoon elephant with a laptop"></div>
  <div class="mascot mascot--dem" style="top:1244px;height:118px;left:665px;width:70px" role="img" aria-label="Cartoon donkey with a laptop"></div>
  <div class="mascot mascot--rep" style="top:1376px" role="img" aria-label="Cartoon elephant in a suit"></div>
  <div class="mascot mascot--dem" style="top:1366px;height:122px" role="img" aria-label="Cartoon donkey in a suit"></div>
  <div class="mascot mascot--rep" style="top:1500px;width:80px;left:476px" role="img" aria-label="Cartoon elephant on the phone"></div>
  <div class="mascot mascot--dem" style="top:1492px;height:122px" role="img" aria-label="Cartoon donkey on the phone"></div>
  <div class="mascot mascot--rep" style="top:1614px" role="img" aria-label="Cartoon elephant holding a ruler"></div>
  <div class="mascot mascot--dem" style="top:1612px;height:118px" role="img" aria-label="Cartoon donkey holding a ruler"></div>
  <div class="mascot mascot--rep" style="top:1736px" role="img" aria-label="Cartoon elephant washing hands"></div>
  <div class="mascot mascot--dem" style="top:1734px;height:118px" role="img" aria-label="Cartoon donkey washing hands"></div>
  <div class="mascot mascot--rep" style="top:1860px;left:474px;width:46px;background:#e0747a" role="img" aria-label="Red hand sanitizer bottle"></div>
  <div class="mascot mascot--dem" style="top:1860px;left:686px;width:46px;background:var(--navy)" role="img" aria-label="Blue hand sanitizer bottle"></div>
  <div class="mascot mascot--rep" style="top:1962px" role="img" aria-label="Cartoon elephant touching its face"></div>
  <div class="mascot mascot--dem" style="top:1956px;height:122px" role="img" aria-label="Cartoon donkey touching its face"></div>

  <section class="question" style="top:2100px">
    <h2 class="question__title question__title--yellow">What does this table show?</h2>
    <p class="question__answer" style="margin-top:10px">No BIG differences. Basically the same patterns.</p>
  </section>

  <footer class="footer">Based on a survey of 400 U.S. adults conducted March 20 - 24th, 2020.</footer>
</div>
</body>
</html>
```